Business Card for a mobile physiotherapy company

I need a layout for a business card for a mobile physiotherapy company.
Slogan is "Mobile Physiotherapy - Your Road To Recovery"
Phone number is 867-555-0142
Email VardenTherapy@postnest.ca (subject to change with website)
Website www.VardenTherapy.ca
My name and credentials: Luke Varden Luke Varden, BSc(kin), MPT, CAFCI, IMS
Information maybe included: Direct Billing, Services including Physiotherapy, IMS, acupuncture
Maybe include facebook and instagram logos
One side with the logo clean and sharp
Other side with details, try not to look too busy, keep everything concise

```html
<!DOCTYPE html>
<html lang="en">
<head>
<meta charset="utf-8">
<title>Varden Therapy – Business Card</title>
<link rel="stylesheet" href="https://fonts.googleapis.com/css2?family=Lato:wght@400;700&family=Roboto:wght@400&display=swap">
<style>
  :root {
    --stage: #1b1b1b;
    --card: #262626;
    --card-edge: #34568c;
    --brand-blue: #3a5f95;
    --ink: #f2f2f2;
    --icon: #4e6a94;
  }
  * { margin: 0; padding: 0; box-sizing: border-box; }
  html, body { width: 1200px; height: 900px; overflow: hidden; }
  body {
    background: var(--stage);
    font-family: "Lato", sans-serif;
    color: var(--ink);
    position: relative;
  }
  .card {
    position: absolute;
    left: 285px;
    width: 630px;
    height: 360px;
    background: linear-gradient(135deg, #2b2b2b 0%, var(--card) 60%, #222 100%);
    border-bottom: 5px solid var(--card-edge);
    box-shadow: 0 14px 30px rgba(0,0,0,0.55);
  }
  .card--front { top: 50px; }
  .card--back { top: 480px; }

  .wordmark {
    font-family: "Lato", sans-serif;
    font-weight: 700;
    color: var(--ink);
    text-transform: uppercase;
    text-align: center;
    line-height: 1.05;
  }
  .card--front .wordmark {
    position: absolute;
    left: 0; right: 0; top: 120px;
    font-size: 54px;
    letter-spacing: 8px;
  }
  .wordmark .wordmark__sub {
    display: block;
    font-size: 0.5em;
    letter-spacing: 0.55em;
    margin-top: 10px;
  }

  .card--back .wordmark {
    position: absolute;
    left: 30px; top: 120px;
    width: 260px;
    font-size: 44px;
    letter-spacing: 5px;
  }
  .divider {
    position: absolute;
    left: 318px; top: 40px;
    width: 2px; height: 270px;
    background: var(--ink);
  }
  .details {
    position: absolute;
    left: 342px; top: 40px;
    width: 270px;
  }
  .details__name {
    font-family: "Roboto", sans-serif;
    font-weight: 400;
    color: var(--brand-blue);
    font-size: 23px;
    line-height: 1.15;
    margin-bottom: 8px;
  }
  .details__services {
    font-size: 14.5px;
    line-height: 1.4;
    margin-bottom: 12px;
  }
  .contact { list-style: none; }
  .contact__item {
    display: flex;
    align-items: center;
    gap: 10px;
    font-size: 15px;
    line-height: 1.65;
  }
  .contact__icon { width: 12px; height: 12px; flex: none; }
</style>
</head>
<body>

<section class="card card--front" aria-label="Card front">
  <div class="wordmark">Varden<span class="wordmark__sub">Therapy</span></div>
</section>

<section class="card card--back" aria-label="Card back">
  <div class="wordmark">Varden<span class="wordmark__sub">Therapy</span></div>
  <div class="divider"></div>
  <div class="details">
    <p class="details__name">Luke Varden, BSc(kin),<br>MPT, CAFCI, IMS</p>
    <p class="details__services">Direct Billing, Services including<br>Physiotherapy, IMS, acupuncture</p>
    <ul class="contact">
      <li class="contact__item">
        <svg class="contact__icon" viewBox="0 0 12 12" aria-hidden="true"><path d="M3 1 L5 3.5 L4 5 Q5.5 7.5 7 8 L8.5 7 L11 9 L9.5 11 Q4 10.5 1 2.5 Z" fill="var(--icon)"/></svg>
        867-555-0142
      </li>
      <li class="contact__item">
        <svg class="contact__icon" viewBox="0 0 12 12" aria-hidden="true"><rect x="1" y="2.5" width="10" height="7" fill="none" stroke="var(--icon)" stroke-width="1.2"/><path d="M1 2.5 L6 6.5 L11 2.5" fill="none" stroke="var(--icon)" stroke-width="1.2"/></svg>
        VardenTherapy@postnest.ca
      </li>
      <li class="contact__item">
        <svg class="contact__icon" viewBox="0 0 12 12" aria-hidden="true"><circle cx="6" cy="6" r="5" fill="none" stroke="var(--icon)" stroke-width="1.1"/><ellipse cx="6" cy="6" rx="2.2" ry="5" fill="none" stroke="var(--icon)" stroke-width="1"/><path d="M1 6 H11" stroke="var(--icon)" stroke-width="1"/></svg>
        www.VardenTherapy.ca
      </li>
    </ul>
  </div>
</section>

</body>
</html>
```